Bootstrap site for Cloud Services company

Hi,

First I'd like you to submit you design of the homepage. If you are the winner, I'll get you do design the rest and code it up in HTML, CSS etc using bootstrap.

Why bootstrap? This will probably mean
that you understand the fundamentals of CSS and know how to
make a good-looking website. Also should mean that you can throw
together this site relatively easily so you can focus on the design
work. I'll need some icons and banner style images done.

There's no server-side coding involved, and there's also no content to write, just put placemarker text wherever appropriate. You must be familiar with bootstrap.

Our business sells Velmora Suite for Business and IT support services.

The icon for our business is attached.

Basically I want you to go by the design of this site
http://lnk.example-short.net/qR7x

However, don't just copy it. I want it to be of a similar layout and
style, but be creative.

I like the simplicity and how it's easy to follow visually.

Just submit the homepage, and if you're successful, I'll get you to
design the rest of the pages for me and code up the pages.

Thanks!

Target Market(s)

We are marketing towards businesses that need their IT managed for them.

Industry/Entity Type

Business

Requirements
Must have
• I like how clean and nice the roboto font is, but it's up to you.

You're welcome to take inspiration from the 'Tarvix Pulse' layout and design. Nice use of white space and layout.

Menu headings at the top are as follows:
Support | Deployment | Training | Development | Contact Us |
About

Home page:

In a similar style of the referenced webpage http://lnk.example-short.net/qR7x, I'd
like a single banner that says "Brisbane's leading Velmora Suite
specialists". In the banner have a computer screen or laptop and a
tablet or smartphone with some 'velmora suite for business' style of
logos coming out of it be creative with some nice design.

Under that, 3 square (or something) icons.
Save Money | Collaborate | Grow
just put some placemarker text in it in a similar fashion to the
reference site.

Just throw some other things in there to fill it up a bit.
Should not have
• http://lnk.example-short.net/qR7x
I don't want the scrolling banner with the site above, static is fine.

I don't like how when the menu is moused-over, the whole page
moves down.

No stock photos of 'successful business people' or 'very attractive
telephone operator waiting to take your call' :)

```html
<!DOCTYPE html>
<html lang="en">
<head>
<meta charset="utf-8">
<title>Nimbara — Velmora Suite specialists</title>
<link href="https://fonts.googleapis.com/css2?family=Lato:wght@300;400;700&display=swap" rel="stylesheet">
<style>
:root{
  --dark:#3a3a3a;
  --dark-2:#333;
  --footer:#3d3d3d;
  --frame:#5a5a5a;
  --white:#fff;
  --blue:#0d4f9e;
  --blue-soft:#a9c6e8;
  --orange:#f0a22a;
  --orange-deep:#d07a12;
  --red:#b32b2b;
  --green:#2f8f2f;
  --text:#333;
  --line:#d6d6d6;
  --panel:#f2f2f2;
}
*{margin:0;padding:0;box-sizing:border-box}
html,body{width:920px;height:1200px;overflow:hidden;background:var(--white)}
body{position:relative;font-family:'Lato',sans-serif;color:var(--text)}
.abs{position:absolute}

.top-band{left:0;top:0;width:920px;height:398px;background:var(--dark)}
.fade-band{left:0;top:398px;width:920px;height:50px;background:linear-gradient(#e6e6e6,#fff)}
.account-links{right:75px;top:9px;font-size:10px;color:#ddd;letter-spacing:.3px}
.account-links span{margin:0 6px}

.header-frame{left:68px;top:30px;width:784px;height:153px;background:var(--frame);border-radius:3px}
.header-panel{left:74px;top:35px;width:772px;height:142px;background:#f7f7f7;border-radius:2px}
.brand{left:86px;top:100px;display:flex;align-items:center;gap:10px}
.brand-dot{width:34px;height:34px;border-radius:50%;background:var(--blue)}
.brand-name{font-size:24px;font-weight:700;color:#222}
.search{left:693px;top:54px;width:143px;height:27px;border:1px solid #ccc;background:#fff;border-radius:2px;font-size:9px;color:#aaa;font-style:italic;padding:7px 12px}
.search svg{position:absolute;right:9px;top:8px}
.nav a{position:absolute;top:126px;height:26px;line-height:26px;font-size:10px;color:#222;text-decoration:none;white-space:nowrap}
.nav a.active{background:var(--blue);color:#fff;width:51px;text-align:center}

.hero-art{left:72px;top:196px;width:300px;height:226px;border-radius:6px;background:linear-gradient(135deg,#f4f4f4,#cfd8e4 60%,#9aa3ad)}
.hero-title{left:378px;top:224px;font-size:25px;font-weight:300;color:var(--orange);white-space:nowrap}
.hero-copy{left:378px;top:266px;width:470px;font-size:9.5px;line-height:18px;color:#e4e4e4}
.hero-btn{left:743px;top:317px;width:99px;height:31px;background:var(--blue-soft);color:#1d2b3a;font-size:13.5px;text-align:center;line-height:31px;border-radius:2px}
.dots{left:751px;top:367px;display:flex;gap:16px}
.dots i{display:block;width:9px;height:9px;border-radius:50%;background:#fff}
.dots i.on{background:var(--orange)}

.rule{left:68px;width:784px;height:1px;background:var(--line)}

.feature{top:470px;width:225px}
.feature h2{display:flex;align-items:center;gap:10px;font-size:26px;font-weight:300;height:46px}
.feature .dash{border-top:1px dashed #999;margin-top:6px}
.feature p{font-size:9.5px;line-height:17.6px;color:#333;padding:9px 0 9px;text-align:justify}
.feature.money h2{color:var(--blue)}
.feature.collab h2{color:var(--orange-deep)}
.feature.grow h2{color:var(--green)}
.vsep{top:474px;width:1px;height:125px;background:#eee}

.about-title{left:75px;top:638px;font-size:20px;font-weight:300;color:var(--red)}
.about-copy{left:75px;top:675px;width:498px;font-size:9.5px;line-height:17.6px;text-align:justify}
.shot{top:738px;height:105px;background:linear-gradient(#f7f7f7,#e7e3da 45%,#f4f4f4);border-bottom:2px solid #222}

.news{left:623px;top:624px;width:224px;height:237px;border:1px solid #e3e3e3;background:#fff;box-shadow:inset 0 0 8px rgba(0,0,0,.05)}
.news h3{font-size:20px;font-weight:300;color:var(--red);padding:14px 0 12px 20px;border-bottom:1px solid #eee}
.news ul{list-style:none;padding:12px 14px 0 20px}
.news li{position:relative;padding-left:19px;font-size:9.5px;line-height:14.5px;margin-bottom:12px;color:#333}
.news li:before{content:"";position:absolute;left:2px;top:4px;width:6px;height:6px;background:#555;transform:rotate(45deg)}

.testimonials-title{left:0;top:906px;width:920px;text-align:center;font-size:14px;font-weight:400;color:var(--orange-deep)}
.quote-box{left:75px;top:935px;width:770px;height:79px;background:var(--panel);border-radius:8px}
.quote-open{left:86px;top:938px;font-size:46px;color:#ccc;font-family:Georgia,serif}
.quote-close{left:808px;top:968px;font-size:46px;color:#ccc;font-family:Georgia,serif}
.quote-text{left:133px;top:950px;width:680px;font-size:9.5px;line-height:16px}
.quote-name{left:710px;top:987px;font-size:10px;color:var(--red)}

.footer{left:0;top:1038px;width:920px;height:128px;background:var(--footer);color:#eee}
.footer h4{position:absolute;font-size:9.5px;font-weight:400;top:20px}
.qcol{position:absolute;top:38px;list-style:none;font-size:10px}
.qcol li{position:relative;padding-left:13px;height:20px;line-height:20px}
.qcol li:before{content:"";position:absolute;left:1px;top:9px;width:3px;height:3px;border-radius:50%;background:#eee}
.social{position:absolute;left:723px;top:38px;list-style:none;font-size:9.5px}
.social li{display:flex;align-items:center;gap:8px;height:20px}
.social i{display:block;width:13px;height:13px;border-radius:2px;background:#8fa6bf}
.social i.rss{background:#e08b2b}
.copyright{left:0;top:1166px;width:920px;height:34px;background:var(--dark-2);color:#bbb;font-size:10px;text-align:center;line-height:32px}
</style>
</head>
<body>
<div class="abs top-band"></div>
<div class="abs fade-band"></div>
<div class="abs account-links">LOG IN<span>|</span>REGISTER</div>

<header>
  <div class="abs header-frame"></div>
  <div class="abs header-panel"></div>
  <div class="abs brand"><span class="brand-dot"></span><span class="brand-name">Nimbara</span></div>
  <div class="abs search">Search
    <svg width="9" height="9" viewBox="0 0 9 9"><circle cx="3.6" cy="3.6" r="2.8" fill="none" stroke="#aaa"/><line x1="5.6" y1="5.6" x2="8.5" y2="8.5" stroke="#aaa"/></svg>
  </div>
  <nav class="nav">
    <a class="active" style="left:297px">HOME</a>
    <a style="left:364px">ABOUT</a>
    <a style="left:425px">SUPPORT</a>
    <a style="left:497px">DEPLOYMENT</a>
    <a style="left:589px">TRAINING</a>
    <a style="left:665px">DEVELOPMENT</a>
    <a style="left:764px">CONTACT US</a>
  </nav>
</header>

<section class="hero">
  <div class="abs hero-art" role="img" aria-label="Desktop monitor and tablet with suite app icons circling the screen"></div>
  <h1 class="abs hero-title">Brisbane's leading Velmora Suite specialists</h1>
  <p class="abs hero-copy">Sed ut perspiciatis unde omnis iste natus error sit voluptatem accusantium doloremque laudantium, totam rem aperiam, eaque ipsa quae ab illo inventore veritatis et quasi architecto beatae vitae dicta.</p>
  <div class="abs hero-btn">View more</div>
  <div class="abs dots"><i class="on"></i><i></i><i></i><i></i></div>
</section>

<div class="abs rule" style="top:453px"></div>

<section>
  <div class="abs feature money" style="left:72px">
    <h2><svg width="24" height="34" viewBox="0 0 24 34"><text x="12" y="28" text-anchor="middle" font-size="32" font-weight="700" fill="#0d4f9e" font-family="Lato,sans-serif">$</text></svg>Save Money</h2>
    <div class="dash"></div>
    <p>Sedomnis iste natus error sit voluptatem accusan tium doloremque laudantium, totam rem aperiam, eaque ipsa quae ab illo inventore veritatis.</p>
    <div class="dash" style="margin-top:0"></div>
  </div>
  <div class="abs vsep" style="left:323px"></div>
  <div class="abs feature collab" style="left:347px">
    <h2><svg width="32" height="30" viewBox="0 0 32 30"><circle cx="20" cy="8" r="6" fill="#9aa8b8"/><path d="M10 28c0-8 4-12 10-12s10 4 10 12z" fill="#9aa8b8"/><circle cx="11" cy="11" r="6" fill="#f0a22a"/><path d="M0 30c0-8 4-12 11-12s11 4 11 12z" fill="#f0a22a"/></svg>Collaborate</h2>
    <div class="dash"></div>
    <p>Sedomnis iste natus error sit voluptatem accusan tium doloremque laudantium, totam rem aperiam, eaque ipsa quae ab illo inventore veritatis.</p>
    <div class="dash" style="margin-top:0"></div>
  </div>
  <div class="abs vsep" style="left:598px"></div>
  <div class="abs feature grow" style="left:622px">
    <h2><svg width="32" height="30" viewBox="0 0 32 30"><rect x="2" y="3" width="26" height="26" fill="#f4f4f4" stroke="#ccc"/><rect x="6" y="16" width="5" height="11" fill="#2f8f2f"/><rect x="13" y="10" width="5" height="17" fill="#f0a22a"/><rect x="20" y="6" width="5" height="21" fill="#0d4f9e"/></svg>Grow</h2>
    <div class="dash"></div>
    <p>Sedomnis iste natus error sit voluptatem accusan tium doloremque laudantium, totam rem aperiam, eaque ipsa quae ab illo inventore veritatis.</p>
    <div class="dash" style="margin-top:0"></div>
  </div>
</section>

<section>
  <h2 class="abs about-title">About us</h2>
  <p class="abs about-copy">Sed ut perspiciatis unde omnis iste natus error sit voluptatem accusantium doloremque laudantium, totam rem aperiam, eaque ipsa quae ab illo inventore veritatis et quasi architecto beatae vitae dicta sunt explicabo. Nemo enim ipsam voluptatem quia voluptas sit aspernatur aut odit aut fugit.</p>
  <div class="abs shot" style="left:75px;width:120px" role="img" aria-label="App card with map and directions"></div>
  <div class="abs shot" style="left:209px;width:108px" role="img" aria-label="App card with sports score"></div>
  <div class="abs shot" style="left:329px;width:121px" role="img" aria-label="App card with map and directions"></div>
  <div class="abs shot" style="left:465px;width:106px" role="img" aria-label="App card with sports score"></div>
</section>

<aside class="abs news">
  <h3>Latest News</h3>
  <ul>
    <li>Atsert vero eos et accusamus et iusto odio dignissimos ducimus qui.</li>
    <li>Atsert vero eos et accusamus et iusto odio dignissimos ducimus qui.</li>
    <li>Atsert vero eos et accusamus et iusto odio dignissimos ducimus qui.</li>
    <li>Atsert vero eos et accusamus et iusto odio dignissimos ducimus qui.</li>
  </ul>
</aside>

<div class="abs rule" style="top:886px"></div>

<section>
  <h2 class="abs testimonials-title">Clients Testimonials</h2>
  <div class="abs quote-box"></div>
  <div class="abs quote-open">“</div>
  <p class="abs quote-text">At vero eos et accusamus et iusto odio dignissimos ducimus qui blanditiis praesentium voluptatum deleniti atque corrupti quos dolores et quas molestias excepturi sint occaecati cupiditate non provident, similique.</p>
  <div class="abs quote-name">Client Name, City</div>
  <div class="abs quote-close">”</div>
</section>

<footer class="abs footer">
  <h4 style="left:76px">Quick Links</h4>
  <ul class="qcol" style="left:77px"><li>Quick Link 1</li><li>Quick Link 2</li><li>Quick Link 3</li><li>Quick Link 4</li></ul>
  <ul class="qcol" style="left:181px"><li>Quick Link 1</li><li>Quick Link 2</li><li>Quick Link 3</li><li>Quick Link 4</li></ul>
  <ul class="qcol" style="left:285px"><li>Quick Link 1</li><li>Quick Link 2</li><li>Quick Link 3</li><li>Quick Link 4</li></ul>
  <ul class="qcol" style="left:389px"><li>Quick Link 1</li><li>Quick Link 2</li><li>Quick Link 3</li><li>Quick Link 4</li></ul>
  <ul class="qcol" style="left:493px"><li>Quick Link 1</li><li>Quick Link 2</li><li>Quick Link 3</li><li>Quick Link 4</li></ul>
  <ul class="qcol" style="left:589px"><li>Quick Link 1</li><li>Quick Link 2</li><li>Quick Link 3</li><li>Quick Link 4</li></ul>
  <h4 style="left:722px">Connect with us</h4>
  <ul class="social">
    <li><i></i>Join with us on Chatterly</li>
    <li><i></i>Foloow us on Chirpwave</li>
    <li><i></i>Connect with Linkora</li>
    <li><i class="rss"></i>Get updated in RSS</li>
  </ul>
</footer>
<div class="abs copyright">Copyright © 2012 www.nimbara-cloud.example. All rights reserved.</div>
</body>
</html>
```